Redesign of business card for Cedar Ridge Mechanical

We are looking for a new design for our business cards for Cedar Ridge Mechanical. We are a plumbing & HVAC construction company, operating on the West Coast of Canada and USA. Logo attached.
Industry/Entity Type
Construction - Plumbing & HVAC
Contact Information for Business Card
Name, address, phone numbers, email, website address
Look and feel
Each slider illustrates characteristics of the customer's brand and the style your logo design should communicate.

```html
<!DOCTYPE html>
<html lang="en">
<head>
<meta charset="utf-8">
<title>Cedar Ridge Mechanical – Business Card</title>
<link href="https://fonts.googleapis.com/css2?family=Arimo:wght@400;700&display=swap" rel="stylesheet">
<style>
  :root {
    --backdrop: #d9d9d9;
    --card-dark: #3a3a3a;
    --card-light: #ffffff;
    --ink-light: #ffffff;
    --ink-muted: #e4e4e4;
    --ink-dark: #111111;
    --rule: #9a9a9a;
  }
  * { margin: 0; padding: 0; box-sizing: border-box; }
  html, body {
    width: 1200px; height: 800px; overflow: hidden;
    background: var(--backdrop);
    font-family: "Arimo", Arial, sans-serif;
  }
  .stage {
    position: relative; width: 1200px; height: 800px;
  }
  .card {
    position: absolute; top: 252px;
    width: 520px; height: 297px;
    border-radius: 18px;
    box-shadow: 0 10px 26px rgba(0,0,0,0.18);
  }
  .card--back { left: 50px; background: var(--card-dark); color: var(--ink-light); }
  .card--front { left: 630px; background: var(--card-light); color: var(--ink-dark); }

  /* back side */
  .brand-mark {
    position: absolute; top: 34px; right: 34px;
    display: flex; align-items: center; gap: 8px;
    font-weight: 700; font-size: 15px; letter-spacing: 0.06em;
    text-transform: uppercase; color: var(--ink-light);
  }
  .brand-mark .square { width: 12px; height: 12px; background: var(--ink-light); }
  .divider {
    position: absolute; left: 34px; right: 34px; top: 176px;
    height: 1px; background: var(--rule);
  }
  .person { position: absolute; left: 34px; top: 128px; }
  .person .name { font-weight: 700; font-size: 21px; line-height: 1.1; }
  .person .title { font-size: 15px; color: var(--ink-muted); line-height: 1.3; }
  .contact-list {
    position: absolute; left: 34px; top: 190px;
    list-style: none; font-size: 14px; line-height: 20px; color: var(--ink-muted);
  }
  .contact-list li { display: flex; align-items: center; gap: 8px; }
  .contact-list svg { width: 12px; height: 12px; flex: none; }
  .address {
    position: absolute; right: 34px; top: 190px;
    text-align: right; font-size: 14px; line-height: 20px; color: var(--ink-muted);
    font-style: normal;
  }

  /* front side */
  .front-brand {
    position: absolute; inset: 0;
    display: flex; align-items: center; justify-content: center; gap: 12px;
  }
  .front-brand .square { width: 26px; height: 26px; background: var(--ink-dark); }
  .front-brand .wordmark {
    font-weight: 700; font-size: 27px; letter-spacing: 0.05em;
    text-transform: uppercase; color: var(--ink-dark);
  }
</style>
</head>
<body>
<main class="stage">
  <section class="card card--back" aria-label="Business card back">
    <div class="brand-mark"><span class="square"></span>Cedar Ridge Mechanical</div>
    <div class="person">
      <p class="name">Daniel Mercer</p>
      <p class="title">President</p>
    </div>
    <div class="divider"></div>
    <ul class="contact-list">
      <li>
        <svg viewBox="0 0 12 12" aria-hidden="true"><path fill="#fff" d="M2.4 0.8l2 0 .8 2.6-1.3 1a6 6 0 0 0 2.7 2.7l1-1.3 2.6.8v2c0 .8-.6 1.4-1.4 1.4A9.2 9.2 0 0 1 1 1.6c0-.5.5-.8 1.4-.8z"/></svg>
        (604) 555-0148
      </li>
      <li>
        <svg viewBox="0 0 12 12" aria-hidden="true"><rect x="0.5" y="2" width="11" height="8" fill="#fff"/><path d="M0.8 2.4L6 6.6l5.2-4.2" fill="none" stroke="#3a3a3a" stroke-width="1"/></svg>
        name@cedarridgemechanical.com
      </li>
      <li>
        <svg viewBox="0 0 12 12" aria-hidden="true"><circle cx="6" cy="6" r="5.5" fill="#fff"/><path d="M0.8 6h10.4M6 0.6c-2.6 3-2.6 7.8 0 10.8M6 0.6c2.6 3 2.6 7.8 0 10.8" fill="none" stroke="#3a3a3a" stroke-width="0.9"/></svg>
        www.cedarridgemechanical.com
      </li>
    </ul>
    <address class="address">
      2710 Alder Street<br>
      Vancouver, BC V6H 3L2
    </address>
  </section>

  <section class="card card--front" aria-label="Business card front">
    <div class="front-brand">
      <span class="square"></span>
      <span class="wordmark">Cedar Ridge Mechanical</span>
    </div>
  </section>
</main>
</body>
</html>
```